business card deign

Logo needs the following on it.
1. attached logo
2. Tagline - "If it keeps a drink cold or the party going...we do it!"
3. Name- Dalton Pikes, Founder and CPO
4. Address - 412 E. Carver Avenue, Ste 2207, Tampa, FL. 33917
5. Phone - 555.318.4726

```html
<!DOCTYPE html>
<html lang="en">
<head>
<meta charset="utf-8">
<title>Hopwell Business Card</title>
<link rel="stylesheet" href="https://fonts.googleapis.com/css2?family=Open+Sans:wght@400;700&display=swap">
<style>
  :root {
    --stage: #232323;
    --card: #1b1b1b;
    --card-edge: #111111;
    --pattern-top: #3a3a3a;
    --pattern-bottom: #141414;
    --ink: #ffffff;
    --ink-soft: #e6e6e6;
  }
  * { box-sizing: border-box; margin: 0; padding: 0; }
  html, body {
    width: 1200px; height: 780px; overflow: hidden;
    background: var(--stage);
    font-family: "Open Sans", sans-serif;
    color: var(--ink);
  }
  .canvas { position: relative; width: 1200px; height: 780px; }
  .card {
    position: absolute;
    width: 560px; height: 320px;
    border-radius: 22px;
    background: var(--card);
    box-shadow: 0 3px 0 var(--card-edge), 0 14px 30px rgba(0,0,0,.45);
    overflow: hidden;
  }
  .card--back { left: 60px; top: 60px; }
  .card--front { left: 580px; top: 400px; }

  .back-pattern {
    position: absolute; inset: 0;
    background: linear-gradient(200deg, var(--pattern-top) 0%, #222 45%, var(--pattern-bottom) 100%);
  }
  .back-brand {
    position: absolute; right: 44px; bottom: 120px;
    display: flex; align-items: center; gap: 6px;
    font-size: 9px; font-weight: 700; letter-spacing: 3px;
    color: var(--ink);
  }
  .back-brand .dot { width: 8px; height: 8px; border-radius: 50%; background: var(--ink); }

  .front-brand {
    position: absolute; right: 44px; top: 48px;
    display: flex; align-items: center; gap: 12px;
    font-size: 34px; font-weight: 700; letter-spacing: 9px;
    color: var(--ink);
  }
  .front-brand .dot { width: 20px; height: 20px; border-radius: 50%; background: var(--ink); }

  .tagline {
    position: absolute; right: 40px; top: 132px; width: 250px;
    font-size: 13px; line-height: 1.35; color: var(--ink-soft);
  }
  .contact {
    position: absolute; right: 30px; top: 186px; width: 260px;
    list-style: none; font-size: 13px; line-height: 1.35; color: var(--ink-soft);
  }
  .contact li { display: flex; gap: 8px; align-items: flex-start; margin-bottom: 4px; }
  .contact svg { flex: none; margin-top: 2px; }

  .person {
    position: absolute; left: 30px; bottom: 24px;
    transform: rotate(-90deg); transform-origin: left bottom;
    translate: 44px 0;
    white-space: nowrap;
  }
  .person__name { font-size: 24px; font-weight: 700; line-height: 1.1; }
  .person__role { font-size: 14px; font-weight: 400; color: var(--ink-soft); }
</style>
</head>
<body>
<main class="canvas">

  <section class="card card--back" aria-label="Card back">
    <div class="back-pattern" role="img" aria-label="Repeating brand mark pattern with a glossy sheen fading from top right"></div>
    <div class="back-brand"><span class="dot"></span>HOPWELL</div>
  </section>

  <section class="card card--front" aria-label="Card front">
    <div class="front-brand"><span class="dot"></span>HOPWELL</div>
    <p class="tagline">If it keeps a drink cold or the party going...we do it!</p>
    <ul class="contact">
      <li>
        <svg width="12" height="12" viewBox="0 0 24 24" aria-hidden="true"><path fill="#fff" d="M6.6 10.8a15.1 15.1 0 0 0 6.6 6.6l2.2-2.2a1 1 0 0 1 1-.25 11.4 11.4 0 0 0 3.6.57 1 1 0 0 1 1 1V20a1 1 0 0 1-1 1A17 17 0 0 1 3 4a1 1 0 0 1 1-1h3.5a1 1 0 0 1 1 1c0 1.25.2 2.45.57 3.57a1 1 0 0 1-.25 1z"/></svg>
        <span>555.318.4726</span>
      </li>
      <li>
        <svg width="12" height="14" viewBox="0 0 24 28" aria-hidden="true"><path fill="none" stroke="#fff" stroke-width="2.5" d="M12 26s8-8.5 8-15a8 8 0 0 0-16 0c0 6.5 8 15 8 15z"/><circle cx="12" cy="11" r="3" fill="#fff"/></svg>
        <span>412 E. Carver Avenue,<br>Ste 2207, Tampa, FL. 33917</span>
      </li>
    </ul>
    <div class="person">
      <p class="person__name">Dalton Pikes</p>
      <p class="person__role">Founder and CPO</p>
    </div>
  </section>

</main>
</body>
</html>
```